CBD AgriBusiness Verdant Trophy Business Card

We are HiTec producer of medical cannabis CBD Switzerland of high quality. Our website is alpinleaf.net, we will also revisit it graphically, the winner of this contest will be the graphic designer chosen for the new design of the website. We stand out by the skill of the team, many of our engineers we win cup cannabis. I join the current map to take as an example but to revisit completely: deletion of surname and first name, modification of funds (front / back), reorganization of text info, highlighting the address of the website. three characteristics define the business card: Professional, Class, refined. The business card must be optimized for soft-touch and selective varnish printing.

Target Market(s)

Customers and Suppliers

Industry/Entity Type

Agribusiness

Contact Information for Business Card

Logo, Tél / Whatsapp, mail, url du site : alpinleaf.net

Font styles to use
Sans Serif

Requirements
Must have
• Logo of alpinleaf.net
Nice to have
• a design that stands out well on the selective varnish
Should not have
• Last name and first name

```html
<!DOCTYPE html>
<html lang="en">
<head>
<meta charset="utf-8">
<title>alpinleaf business card</title>
<link rel="stylesheet" href="https://fonts.googleapis.com/css2?family=Montserrat:wght@800&family=Roboto:wght@400;500&display=swap">
<style>
  :root {
    --backdrop: #b9b9bb;
    --card-dark: #58585b;
    --card-dark-deep: #47474a;
    --card-light: #ffffff;
    --accent-green: #7cc04b;
    --text-light: #ffffff;
    --text-dark: #4a4a4d;
  }
  * { box-sizing: border-box; margin: 0; padding: 0; }
  html, body {
    width: 1200px; height: 930px; overflow: hidden;
    background: var(--backdrop);
    font-family: "Roboto", sans-serif;
  }
  .canvas { position: relative; width: 1200px; height: 930px; }
  .card {
    position: absolute; width: 520px; height: 300px;
    border-radius: 22px; overflow: hidden;
    box-shadow: 0 6px 14px rgba(0,0,0,.25);
  }
  .card-back {
    left: 90px; top: 150px;
    background: linear-gradient(120deg, var(--card-dark-deep), var(--card-dark) 55%, var(--card-dark-deep));
    display: flex; align-items: center; justify-content: center;
  }
  .card-front { left: 590px; top: 480px; background: var(--card-dark); }
  .card-front svg.front-shape { position: absolute; inset: 0; }
  .brand { display: flex; align-items: center; gap: 10px; }
  .brand-square { width: 26px; height: 26px; background: var(--accent-green); }
  .brand-name {
    font-family: "Montserrat", sans-serif; font-weight: 800;
    font-size: 52px; letter-spacing: -1px; line-height: 1;
  }
  .card-back .brand-name { color: var(--text-light); }
  .card-front .brand { position: absolute; top: 40px; right: 40px; }
  .card-front .brand-square { width: 18px; height: 18px; }
  .card-front .brand-name { font-size: 38px; color: var(--text-dark); }
  .contact-block {
    position: absolute; left: 34px; bottom: 26px;
    color: var(--text-light); font-size: 12.5px; line-height: 1.45;
  }
  .person-role {
    font-weight: 500; font-size: 15px; letter-spacing: .5px;
    text-transform: uppercase; margin-bottom: 10px;
  }
  .address { margin-bottom: 10px; }
  .contact-line { display: flex; align-items: center; gap: 8px; }
  .contact-line svg { width: 11px; height: 11px; flex: none; }
  .contact-line.web { font-weight: 500; font-size: 14px; }
</style>
</head>
<body>
<main class="canvas">
  <section class="card card-back" aria-label="Card back">
    <div class="brand">
      <span class="brand-square"></span>
      <span class="brand-name">alpinleaf</span>
    </div>
  </section>

  <section class="card card-front" aria-label="Card front">
    <svg class="front-shape" width="520" height="300" viewBox="0 0 520 300" aria-hidden="true">
      <path d="M145 0 C 185 122, 330 205, 520 215 L 520 0 Z" fill="var(--card-light)"/>
      <path d="M142 0 C 182 124, 328 208, 520 217" fill="none" stroke="var(--accent-green)" stroke-width="5"/>
    </svg>
    <div class="brand">
      <span class="brand-square"></span>
      <span class="brand-name">alpinleaf</span>
    </div>
    <div class="contact-block">
      <p class="person-role">Director</p>
      <p class="address">48b Harbour Lane,<br>Ashford, NZ, 7020</p>
      <p class="contact-line">
        <svg viewBox="0 0 12 12"><path d="M2 1 L4 1 L5 4 L3.6 5 C4.3 6.6 5.4 7.7 7 8.4 L8 7 L11 8 L11 10 C11 10.6 10.6 11 10 11 C5.6 11 1 6.4 1 2 C1 1.4 1.4 1 2 1 Z" fill="currentColor"/></svg>
        +41 (0) 70 555 12 34
      </p>
      <p class="contact-line">
        <svg viewBox="0 0 12 12"><rect x="3" y="1" width="6" height="10" rx="1" fill="none" stroke="currentColor" stroke-width="1.2"/><circle cx="6" cy="9.3" r=".7" fill="currentColor"/></svg>
        +44 7700 90 01 23
      </p>
      <p class="contact-line">
        <svg viewBox="0 0 12 12"><rect x="1" y="2.5" width="10" height="7" fill="none" stroke="currentColor" stroke-width="1.2"/><path d="M1 2.5 L6 6.5 L11 2.5" fill="none" stroke="currentColor" stroke-width="1.2"/></svg>
        office@alpinleaf.net
      </p>
      <p class="contact-line web">
        <svg viewBox="0 0 12 12"><circle cx="6" cy="6" r="5" fill="none" stroke="currentColor" stroke-width="1.1"/><path d="M1 6 H11 M6 1 C3.5 3.5 3.5 8.5 6 11 M6 1 C8.5 3.5 8.5 8.5 6 11" fill="none" stroke="currentColor" stroke-width="1"/></svg>
        www.alpinleaf.net
      </p>
    </div>
  </section>
</main>
</body>
</html>
```